Treatment Info-Graphic Poster

22 x 28 poster. We need a design for a poster to hang in our treatment rooms that quickly compares different treatments we offer and sets expectations for the patient. Attached is something I very quickly created on Excel, but we would like one that matches our company colors and looks much more polished. I have attached a info-graphic we have had designed prior for reference.

Target Market(s)

Osteoarthritis of the knee patients treatment comparison info graphic for poster

Font styles to use
Serif

Colors
85cae6
f78f20

Requirements
Must have
• Branded treatment comparison table
Nice to have
• Treatment graphics

```html
<!DOCTYPE html>
<html lang="en">
<head>
<meta charset="utf-8">
<title>Knee OA Treatment Comparison</title>
<link href="https://fonts.googleapis.com/css2?family=Zilla+Slab:wght@300;400;500;600;700&family=Lato:wght@400;700&display=swap" rel="stylesheet">
<style>
  :root{
    --teal:#42a5bd;
    --teal-pale:#e8f4f8;
    --orange:#f7931f;
    --charcoal:#4a4a4a;
    --ink:#454545;
    --white:#ffffff;
  }
  *{box-sizing:border-box;margin:0;padding:0}
  html,body{width:1200px;height:848px;overflow:hidden}
  body{position:relative;background:var(--teal);font-family:"Zilla Slab",Georgia,serif;color:var(--ink)}

  .masthead{position:absolute;left:0;top:0;width:1200px;height:176px;background:var(--teal-pale)}
  .brand{position:absolute;left:73px;top:40px;width:193px;text-align:center}
  .brand-name{display:block;font-family:"Zilla Slab",serif;font-weight:600;font-size:58px;line-height:1;color:var(--teal);letter-spacing:-1px}
  .brand-tagline{display:block;margin-top:28px;font-family:"Lato",sans-serif;font-size:15px;color:#333}
  .title{position:absolute;left:310px;top:38px;color:#555}
  .title-main{font-weight:700;font-size:47px;line-height:1}
  .title-sub{font-weight:300;font-size:35px;line-height:1;margin-top:8px;color:#5a5a5a}
  .claim{position:absolute;right:69px;top:55px;text-align:right}
  .claim-line{font-weight:700;font-size:19px;color:var(--orange)}
  .claim-url{margin-top:12px;font-weight:600;font-size:13.5px;color:#333}

  .grid{position:absolute;left:62px;top:203px;display:grid;
    grid-template-columns:289px 188px 188px 188px 188px;column-gap:7px}
  .col-head{height:29px;line-height:29px;padding-left:12px;font-weight:700;font-size:14px;color:var(--white);white-space:nowrap}
  .col-head.orange{background:var(--orange);text-align:center;padding-left:0}
  .col-head.dark{background:var(--charcoal)}
  .col-head.dark.center{text-align:center;padding-left:0}
  .options{height:82px;background:var(--white);padding:4px 10px 0 5px;font-size:7px;font-family:"Lato",sans-serif;color:#333}
  .options .grade-label{text-align:right;font-family:"Zilla Slab",serif;font-weight:700;font-size:7.5px;color:var(--teal);border-bottom:1px solid #ccc;padding-bottom:2px;margin:0 -10px 5px -5px;padding-right:10px}
  .options.ha .grade-label{color:var(--orange)}
  .options ul{list-style:none}
  .options li{display:flex;justify-content:space-between;line-height:13.5px;padding-left:8px;position:relative}
  .options li.bullet::before{content:"";position:absolute;left:1px;top:5px;width:3px;height:3px;border-radius:50%;background:var(--orange)}
  .options li b{font-weight:700;width:28px}

  .rows{position:absolute;left:62px;top:326px;display:grid;
    grid-template-columns:289px 188px 188px 188px 188px;column-gap:7px;row-gap:6.3px;grid-auto-rows:34px}
  .label{background:var(--white);padding-left:21px;display:flex;align-items:center;font-weight:500;font-size:13.5px;color:var(--ink)}
  .cell{display:flex;align-items:center;justify-content:center}
  .cell.orange{background:var(--orange)}
  .cell.white{background:var(--white)}
  .tick{width:30px;height:24px;fill:none;stroke-width:5.5;stroke-linecap:round;stroke-linejoin:round}
  .orange .tick{stroke:var(--white)}
  .white .tick{stroke:var(--teal)}

  .disclaimer{position:absolute;left:100px;top:782px;width:1000px;text-align:center;color:var(--white);font-size:13px;line-height:16.5px}
  .paren{position:absolute;top:770px;font-weight:300;font-size:46px;color:var(--orange);line-height:1}
  .paren.left{left:100px}
  .paren.right{right:70px}
</style>
</head>
<body>
<header class="masthead">
  <div class="brand">
    <span class="brand-name">kinetra</span>
    <span class="brand-tagline">Move freely again.</span>
  </div>
  <div class="title">
    <h1 class="title-main">Knee OA</h1>
    <p class="title-sub">Treatment Comparison</p>
  </div>
  <div class="claim">
    <p class="claim-line">Your Local Knee Care Team</p>
    <p class="claim-url">www.kinetraknees.com</p>
  </div>
</header>

<section class="grid">
  <div></div>
  <div class="col-head orange">Hyaluronic Acid (HA)</div>
  <div class="col-head dark center">Platelet RichPlasma (PRP)</div>
  <div class="col-head orange">Stem Cell Therapy &amp; PRP</div>
  <div class="col-head dark">Knee Brace(s)</div>

  <div></div>
  <div class="options ha"><div class="grade-label">OA Grade</div><ul>
    <li class="bullet"><span>Single Injection (Arvelon One)</span><b>1,2,3,4</b></li>
    <li class="bullet"><span>Single Injection (Lubrevia)</span><b>1,2,3,4</b></li>
    <li class="bullet"><span>3 Part Injection Series (Trisonel)</span><b>1,2,3,4</b></li>
    <li class="bullet"><span>3/4 Part Injection Series (Corvanta)</span><b>1,2,3,4</b></li>
  </ul></div>
  <div class="options"><div class="grade-label">OA Grade</div><ul>
    <li class="bullet"><span>Single Injection (Plasmiva)</span><b>1, 2</b></li>
    <li class="bullet"><span>2 Part Injection Series</span><b>2, 3</b></li>
  </ul></div>
  <div class="options"><div class="grade-label">OA Grade</div><ul>
    <li class="bullet"><span>Single Injection</span><b>1, 2, 3, 4</b></li>
  </ul></div>
  <div class="options"><div class="grade-label">OA Grade</div><ul>
    <li class="bullet"><span>Stridewell 2</span><b>1, 2, 3, 4</b></li>
    <li><span>Patellar Stabilization</span><b>1, 2, 3, 4</b></li>
  </ul></div>
</section>

<section class="rows">
  <div class="label">Cushion &amp; Lubricate</div>
  <div class="cell orange"><svg class="tick" viewBox="0 0 30 24"><path d="M4 12l8 8L26 5"/></svg></div>
  <div class="cell white"><svg class="tick" viewBox="0 0 30 24"><path d="M4 12l8 8L26 5"/></svg></div>
  <div class="cell orange"><svg class="tick" viewBox="0 0 30 24"><path d="M4 12l8 8L26 5"/></svg></div>
  <div class="cell white"></div>

  <div class="label">Decrease Inflammation</div>
  <div class="cell orange"><svg class="tick" viewBox="0 0 30 24"><path d="M4 12l8 8L26 5"/></svg></div>
  <div class="cell white"><svg class="tick" viewBox="0 0 30 24"><path d="M4 12l8 8L26 5"/></svg></div>
  <div class="cell orange"><svg class="tick" viewBox="0 0 30 24"><path d="M4 12l8 8L26 5"/></svg></div>
  <div class="cell white"></div>

  <div class="label">Stimulates Synovial Production of HA</div>
  <div class="cell orange"><svg class="tick" viewBox="0 0 30 24"><path d="M4 12l8 8L26 5"/></svg></div>
  <div class="cell white"><svg class="tick" viewBox="0 0 30 24"><path d="M4 12l8 8L26 5"/></svg></div>
  <div class="cell orange"><svg class="tick" viewBox="0 0 30 24"><path d="M4 12l8 8L26 5"/></svg></div>
  <div class="cell white"></div>

  <div class="label">Healing Properties</div>
  <div class="cell orange"></div>
  <div class="cell white"><svg class="tick" viewBox="0 0 30 24"><path d="M4 12l8 8L26 5"/></svg></div>
  <div class="cell orange"><svg class="tick" viewBox="0 0 30 24"><path d="M4 12l8 8L26 5"/></svg></div>
  <div class="cell white"></div>

  <div class="label">Repairative Properties</div>
  <div class="cell orange"></div>
  <div class="cell white"></div>
  <div class="cell orange"><svg class="tick" viewBox="0 0 30 24"><path d="M4 12l8 8L26 5"/></svg></div>
  <div class="cell white"></div>

  <div class="label">Potential Cartilage Regeneration</div>
  <div class="cell orange"></div>
  <div class="cell white"></div>
  <div class="cell orange"><svg class="tick" viewBox="0 0 30 24"><path d="M4 12l8 8L26 5"/></svg></div>
  <div class="cell white"></div>

  <div class="label">On Average, Benefits Last 4-6 Months</div>
  <div class="cell orange"><svg class="tick" viewBox="0 0 30 24"><path d="M4 12l8 8L26 5"/></svg></div>
  <div class="cell white"><svg class="tick" viewBox="0 0 30 24"><path d="M4 12l8 8L26 5"/></svg></div>
  <div class="cell orange"><svg class="tick" viewBox="0 0 30 24"><path d="M4 12l8 8L26 5"/></svg></div>
  <div class="cell white"><svg class="tick" viewBox="0 0 30 24"><path d="M4 12l8 8L26 5"/></svg></div>

  <div class="label">On Average, Benefits Last 6-12 Months</div>
  <div class="cell orange"></div>
  <div class="cell white"><svg class="tick" viewBox="0 0 30 24"><path d="M4 12l8 8L26 5"/></svg></div>
  <div class="cell orange"><svg class="tick" viewBox="0 0 30 24"><path d="M4 12l8 8L26 5"/></svg></div>
  <div class="cell white"><svg class="tick" viewBox="0 0 30 24"><path d="M4 12l8 8L26 5"/></svg></div>

  <div class="label">On Average, Benefits Last 18+ Months</div>
  <div class="cell orange"></div>
  <div class="cell white"></div>
  <div class="cell orange"><svg class="tick" viewBox="0 0 30 24"><path d="M4 12l8 8L26 5"/></svg></div>
  <div class="cell white"><svg class="tick" viewBox="0 0 30 24"><path d="M4 12l8 8L26 5"/></svg></div>

  <div class="label">Corrects Biomechanics &amp; Stabilizes Joint</div>
  <div class="cell orange"></div>
  <div class="cell white"></div>
  <div class="cell orange"></div>
  <div class="cell white"><svg class="tick" viewBox="0 0 30 24"><path d="M4 12l8 8L26 5"/></svg></div>

  <div class="label">Covered by MOST Insurance</div>
  <div class="cell orange"><svg class="tick" viewBox="0 0 30 24"><path d="M4 12l8 8L26 5"/></svg></div>
  <div class="cell white"></div>
  <div class="cell orange"></div>
  <div class="cell white"><svg class="tick" viewBox="0 0 30 24"><path d="M4 12l8 8L26 5"/></svg></div>
</section>

<span class="paren left">(</span>
<p class="disclaimer">Treatment outcomes vary by individual. Treatment benefits and length of efficacy are not guaranteed. In some cases, patient's do not respond to treatment.<br>Multiple treatments may be recommended or necessary for the best outcomes.</p>
<span class="paren right">)</span>
</body>
</html>
```